Organization and people consulting firm needs a website design

I need a website that promotes and explains the consulting service we will provide. The organization is called Bluefinch Advisory Partners. Our services include organization design, employee experience, change management, and executive coaching. I would like to see a simple clean and professional design, that reflects a modern and forward looking professional services company

Target Market(s)

Mid market and large companies

Industry/Entity Type

Management Consulting

Coding

Coded - Design and coding required

Number of Pages Required

5+ page

Font styles to use
Sans Serif

Colors

Designer to choose colors to be used in the design.

Requirements
Must have
• The following pages: Home, The Way We Work, What We Do, Our Founder, Insights, Contact.
• Search button.
• Hyper links (will be provided with main body text)
• Scrolling website with summaries at top level and links to more detail at lower level (like this website: veltracore.com)
• Company logo (uploaded)
• I have text for each of the pages that I can upload once the basic design is done
Should not have
• No clutter, keep the design clean

```html
<!DOCTYPE html>
<html lang="en">
<head>
<meta charset="utf-8">
<title>Bluefinch Advisory Partners</title>
<link href="https://fonts.googleapis.com/css2?family=Cinzel:wght@400;700&family=Open+Sans:wght@400;600;700&display=swap" rel="stylesheet">
<style>
:root{
  --red:#d0103a;
  --ink:#222;
  --text:#666;
  --muted:#999;
  --line:#cfcfcf;
  --paper:#fff;
  --gray-bg:#f1f1f1;
  --nav-bg:#1c1c1c;
  --footer-bg:#111;
}
*{box-sizing:border-box;margin:0;padding:0}
a{text-decoration:none}
html,body{width:1200px;height:3991px;overflow:hidden}
body{font-family:"Open Sans",Arial,sans-serif;color:var(--text);background:var(--paper);position:relative}
section,header,footer{position:absolute;left:0;width:1200px}
.section-title{position:absolute;left:0;width:100%;text-align:center;font-family:"Cinzel",Georgia,serif;font-size:40px;color:var(--ink);letter-spacing:1px;font-weight:400;text-transform:uppercase}
.body-copy{font-size:14px;line-height:29px;text-align:center;color:var(--muted)}
.btn-solid{position:absolute;display:flex;align-items:center;justify-content:center;background:var(--red);color:#fff;font-size:14px;font-weight:700;text-transform:uppercase;letter-spacing:.5px}
/* nav */
.site-header{top:0;height:98px;background:var(--nav-bg)}
.brand{position:absolute;left:100px;top:24px;display:flex;align-items:center;gap:14px;color:#fff;font-family:"Cinzel",Georgia,serif;font-weight:400}
.brand-mark{width:40px;height:40px;background:#fff}
.brand-name{display:flex;flex-direction:column;line-height:1}
.brand-name .big{font-size:30px;letter-spacing:.5px}
.brand-name .small{font-size:10px;letter-spacing:3.2px;margin-top:5px;text-transform:uppercase}
.main-nav{position:absolute;left:487px;top:38px;display:flex;font-size:15px;color:#eee}
.main-nav a{color:#eee;margin-right:23px}
.main-nav a.active{color:var(--red)}
.search{position:absolute;left:1086px;top:39px}
/* hero */
.hero{top:98px;height:540px}
.hero-photo{position:absolute;inset:0;background:linear-gradient(180deg,#6e6e6e 0%,#555 45%,#3e3e3e 100%)}
.hero-shade{position:absolute;inset:0;background:rgba(0,0,0,.25)}
.hero h1{position:absolute;top:140px;width:100%;text-align:center;font-family:"Cinzel",Georgia,serif;font-weight:400;font-size:52px;color:#fff;letter-spacing:2px}
.hero p{position:absolute;top:224px;width:100%;text-align:center;font-size:27px;color:#fff}
.btn-outline-light{position:absolute;left:515px;top:291px;width:170px;height:53px;border:2px solid #fff;color:#fff;display:flex;align-items:center;justify-content:center;font-size:15px;font-weight:700;text-transform:uppercase}
/* way we work */
.way{top:638px;height:551px;background:var(--paper)}
.way-frame{position:absolute;left:98px;top:86px;width:1001px;height:327px;border:1px solid var(--red)}
.way .section-title{top:134px}
.way .body-copy{position:absolute;left:200px;top:202px;width:800px}
/* what we do */
.services{top:1189px;height:479px;background:var(--gray-bg)}
.services .section-title{top:74px}
.service-card{position:absolute;top:160px;width:237px;height:239px;border:1px solid var(--line);background:var(--gray-bg);text-align:center}
.service-card.featured{border-color:var(--red)}
.service-card svg.icon{position:absolute;left:98px;top:24px}
.service-card h3{position:absolute;top:88px;width:100%;font-size:17px;font-weight:600;color:#333}
.service-card.featured h3,.service-card.featured p{color:var(--red)}
.service-card p{position:absolute;top:125px;left:22px;right:22px;font-size:13px;line-height:25px;color:var(--muted)}
.service-card .more{position:absolute;left:107px;top:190px}
/* founder */
.founder{top:1668px;height:798px;background:var(--paper)}
.founder .section-title{top:84px}
.portrait{position:absolute;left:493px;top:165px;width:212px;height:212px;border-radius:50%;border:4px solid #e4e4e4;background:linear-gradient(180deg,#cfd3d6,#9aa3aa)}
.founder-name{position:absolute;top:398px;width:100%;text-align:center;font-size:20px;font-weight:700;color:#333}
.founder .body-copy{position:absolute;left:200px;top:456px;width:800px}
/* insights */
.insights{top:2466px;height:811px;background:var(--gray-bg)}
.insights .section-title{top:72px}
.post{position:absolute;top:170px;width:484px}
.post-photo{width:484px;height:277px;border:5px solid #fff;box-shadow:0 0 0 1px #ccc}
.post h3{margin-top:36px;font-size:21px;font-weight:700;color:#333}
.post-meta{margin-top:14px;display:flex;align-items:center;gap:8px;font-size:13px;color:#555}
.post-meta .sep{margin:0 4px}
.post p{margin-top:16px;font-size:13px;line-height:25px;color:#777}
.btn-outline{display:inline-flex;margin-top:30px;width:155px;height:48px;border:1px solid var(--red);color:var(--red);align-items:center;justify-content:center;font-size:14px;font-weight:700;text-transform:uppercase}
/* contact */
.contact{top:3277px;height:455px}
.contact-photo{position:absolute;inset:0;background:linear-gradient(135deg,#3a3a3a,#2a2a2a 60%,#333)}
.contact .section-title{top:54px;color:#fff}
.field{position:absolute;background:#fff;font-size:13px;color:#555;padding:11px 14px}
/* footer */
.site-footer{top:3732px;height:259px;background:var(--footer-bg);color:#fff}
.info{position:absolute;top:50px;display:flex;align-items:center;gap:16px;font-size:13px;line-height:22px}
.ring{width:42px;height:42px;border-radius:50%;border:1px solid #fff;display:flex;align-items:center;justify-content:center}
.footer-nav{position:absolute;top:126px;width:100%;text-align:center;font-size:14px}
.footer-nav span.sep{margin:0 13px}
.rule{position:absolute;left:98px;top:175px;width:1001px;height:1px;background:#333}
.copyright{position:absolute;left:98px;top:204px;font-size:12px}
.social{position:absolute;left:967px;top:197px;display:flex;gap:10px}
.social span{width:26px;height:26px;border-radius:50%;border:1px solid #ccc}
</style>
</head>
<body>

<header class="site-header">
  <div class="brand"><span class="brand-mark"></span><span class="brand-name"><span class="big">Bluefinch</span><span class="small">Advisory Partners</span></span></div>
  <nav class="main-nav">
    <a class="active" href="#">Home</a><a href="#">The Way We Work</a><a href="#">What We Do</a><a href="#">Our Founder</a><a href="#">Insights</a><a href="#">Contact</a>
  </nav>
  <svg class="search" width="16" height="16" viewBox="0 0 16 16"><circle cx="6.5" cy="6.5" r="5" fill="none" stroke="#fff" stroke-width="2"/><line x1="10.3" y1="10.3" x2="15" y2="15" stroke="#fff" stroke-width="2.5"/></svg>
</header>

<section class="hero">
  <div class="hero-photo" role="img" aria-label="Grayscale photo of an open-plan office with people at desks"></div>
  <div class="hero-shade"></div>
  <h1>Bluefinch Advisory Partners</h1>
  <p>We are organisation &amp; people consulting firm</p>
  <a class="btn-outline-light" href="#">Get more info</a>
</section>

<section class="way">
  <div class="way-frame"></div>
  <h2 class="section-title">The Way We Work</h2>
  <p class="body-copy">At vero eos et accusamus et iusto odio dignissimos ducimus qui blanditiis praesentium voluptatum deleniti atque corrupti quos dolores et quas molestias excepturi sint occaecati cupiditate non provident, similique sunt in culpa qui officia deserunt mollitia animi, id est laborum et dolorum fuga. Et harum quidem rerum facilis est et expedita distinctio. Nam libero tempore, cum soluta nobis est eligendi optio cumque nihil impedit quo minus id quod maxime placeat facere possimus, omnis voluptas assimus id quodsumenda est, omnis dolor.</p>
  <a class="btn-solid" href="#" style="left:519px;top:389px;width:162px;height:48px">Learn more</a>
</section>

<section class="services">
  <h2 class="section-title">What We Do</h2>
  <div class="service-card" style="left:98px">
    <svg class="icon" width="40" height="40" viewBox="0 0 40 40"><circle cx="20" cy="20" r="18" fill="#555"/><path d="M10 14c4-2 6 2 9 1s3 5 0 7-2 6-5 7M24 8c2 3 6 3 8 8-3 1-4 5-2 8" fill="none" stroke="#f1f1f1" stroke-width="2.5"/></svg>
    <h3>Organisation design</h3>
    <p>Nam libero tempore, cum soluta nobis est eligendi opticu</p>
    <svg class="more" width="22" height="22" viewBox="0 0 22 22"><circle cx="11" cy="11" r="10" fill="#bbb"/><path d="M11 6v10M6 11h10" stroke="#fff" stroke-width="2"/></svg>
  </div>
  <div class="service-card featured" style="left:354px">
    <svg class="icon" width="40" height="40" viewBox="0 0 40 40"><path d="M20 2l5.3 11.6 12.7 1.3-9.5 8.6 2.7 12.5L20 29.6 8.8 36l2.7-12.5L2 14.9l12.7-1.3z" fill="var(--red)"/></svg>
    <h3>Employee Experience</h3>
    <p>Nam libero tempore, cum soluta nobis est eligendi opticu</p>
    <svg class="more" width="22" height="22" viewBox="0 0 22 22"><circle cx="11" cy="11" r="10" fill="var(--red)"/><path d="M11 6v10M6 11h10" stroke="#fff" stroke-width="2"/></svg>
  </div>
  <div class="service-card" style="left:609px">
    <svg class="icon" width="44" height="40" viewBox="0 0 44 40"><circle cx="22" cy="9" r="6" fill="#555"/><circle cx="9" cy="13" r="5" fill="#555"/><circle cx="35" cy="13" r="5" fill="#555"/><path d="M12 36c0-10 4-15 10-15s10 5 10 15z" fill="#555"/><path d="M0 34c0-9 3-13 9-13 2 0 3 1 4 1-2 3-3 7-3 12zM44 34c0-9-3-13-9-13-2 0-3 1-4 1 2 3 3 7 3 12z" fill="#555"/></svg>
    <h3>Change Management</h3>
    <p>Nam libero tempore, cum soluta nobis est eligendi opticu</p>
    <svg class="more" width="22" height="22" viewBox="0 0 22 22"><circle cx="11" cy="11" r="10" fill="#bbb"/><path d="M11 6v10M6 11h10" stroke="#fff" stroke-width="2"/></svg>
  </div>
  <div class="service-card" style="left:865px">
    <svg class="icon" width="40" height="40" viewBox="0 0 40 40"><circle cx="20" cy="11" r="9" fill="#555"/><path d="M5 38c0-12 6-17 15-17s15 5 15 17z" fill="#555"/></svg>
    <h3>Executive Coaching</h3>
    <p>Nam libero tempore, cum soluta nobis est eligendi opticu</p>
    <svg class="more" width="22" height="22" viewBox="0 0 22 22"><circle cx="11" cy="11" r="10" fill="#bbb"/><path d="M11 6v10M6 11h10" stroke="#fff" stroke-width="2"/></svg>
  </div>
</section>

<section class="founder">
  <h2 class="section-title">Our Founder</h2>
  <div class="portrait" role="img" aria-label="Portrait photo of the founder"></div>
  <div class="founder-name">JOHN DOE</div>
  <p class="body-copy">At vero eos et accusamus et iusto odio dignissimos ducimus qui blanditiis praesentium voluptatum deleniti atque corrupti quos dolores et quas molestias excepturi sint occaecati cupiditate non provident, similique sunt in culpa qui officia deserunt mollitia animi, id est laborum et dolorum fuga. Et harum quidem rerum facilis est et expedita distinctio. Nam libero tempore, cum soluta nobis est eligendi optio cumque nihil impedit quo minus id quod maxime placeat facere possimus, omnis voluptas assimus id quodsumenda est, omnis dolor.</p>
  <a class="btn-solid" href="#" style="left:519px;top:654px;width:162px;height:51px">Learn more</a>
</section>

<section class="insights">
  <h2 class="section-title">Insights</h2>
  <article class="post" style="left:98px">
    <div class="post-photo" role="img" aria-label="Photo of sticky notes and papers laid out on a wooden table" style="background:linear-gradient(135deg,#6b4a35,#b59a86 50%,#d6b8b3)"></div>
    <h3>FINIBUS BONODICTA&nbsp; RUM ET MALORUM</h3>
    <div class="post-meta">
      <svg width="13" height="13" viewBox="0 0 13 13"><rect x="1" y="2" width="11" height="10" fill="var(--red)"/><rect x="2.5" y="5" width="8" height="5.5" fill="#fff"/></svg>11/04/2018<span class="sep">|</span>
      <svg width="12" height="13" viewBox="0 0 12 13"><circle cx="6" cy="3.5" r="3" fill="var(--red)"/><path d="M0 13c0-5 2.5-7 6-7s6 2 6 7z" fill="var(--red)"/></svg>John Doe
    </div>
    <p>Neque porro quisquam est, qui dolorem ipsum quia dolor sit amet sectetur, adipisci velit, sed quia non numquam eius modi tempora incidunt utlabore et dolore magnam aliquam quaerat voluptatem.</p>
    <a class="btn-outline" href="#">Learn more</a>
  </article>
  <article class="post" style="left:617px">
    <div class="post-photo" role="img" aria-label="Photo of a hand reviewing printed charts with a pen" style="background:linear-gradient(135deg,#7e9bb3,#d9e3ea 55%,#b8c7d3)"></div>
    <h3>FINIBUS BONODICTA&nbsp; RUM ET MALORUM</h3>
    <div class="post-meta">
      <svg width="13" height="13" viewBox="0 0 13 13"><rect x="1" y="2" width="11" height="10" fill="var(--red)"/><rect x="2.5" y="5" width="8" height="5.5" fill="#fff"/></svg>11/04/2018<span class="sep">|</span>
      <svg width="12" height="13" viewBox="0 0 12 13"><circle cx="6" cy="3.5" r="3" fill="var(--red)"/><path d="M0 13c0-5 2.5-7 6-7s6 2 6 7z" fill="var(--red)"/></svg>John Doe
    </div>
    <p>Neque porro quisquam est, qui dolorem ipsum quia dolor sit amet sectetur, adipisci velit, sed quia non numquam eius modi tempora incidunt utlabore et dolore magnam aliquam quaerat voluptatem.</p>
    <a class="btn-outline" href="#">Learn more</a>
  </article>
</section>

<section class="contact">
  <div class="contact-photo" role="img" aria-label="Dark photo of a desk with a laptop"></div>
  <h2 class="section-title">Contact</h2>
  <div class="field" style="left:258px;top:133px;width:333px;height:40px">First Name</div>
  <div class="field" style="left:607px;top:133px;width:333px;height:40px">Last Name</div>
  <div class="field" style="left:258px;top:186px;width:333px;height:40px">Email Address</div>
  <div class="field" style="left:607px;top:186px;width:333px;height:40px">Phone Number</div>
  <div class="field" style="left:258px;top:240px;width:682px;height:79px">Message</div>
  <a class="btn-solid" href="#" style="left:519px;top:341px;width:162px;height:43px;border-radius:22px">Contact us</a>
</section>

<footer class="site-footer">
  <div class="info" style="left:185px">
    <div class="ring"><svg width="14" height="18" viewBox="0 0 14 18"><path d="M7 0C3 0 0 3 0 7c0 5 7 11 7 11s7-6 7-11c0-4-3-7-7-7z" fill="#fff"/><circle cx="7" cy="7" r="2.5" fill="#111"/></svg></div>
    <div>At vero eos et accu<br>samus et iusto odio dimos ducimu</div>
  </div>
  <div class="info" style="left:515px">
    <div class="ring"><svg width="16" height="16" viewBox="0 0 16 16"><path d="M3 1l3 3-2 2c1 2 4 5 6 6l2-2 3 3-2 2C7 15 1 9 1 3z" fill="#fff"/></svg></div>
    <div>1 555 014 2290</div>
  </div>
  <div class="info" style="left:720px">
    <div class="ring"><svg width="16" height="12" viewBox="0 0 16 12"><rect width="16" height="12" rx="1" fill="#fff"/><path d="M0 1l8 6 8-6" fill="none" stroke="#111" stroke-width="1.5"/></svg></div>
    <div>info@bluefinchadvisorypartners.com</div>
  </div>
  <nav class="footer-nav">Home<span class="sep">|</span>The Way We Work<span class="sep">|</span>What We Do<span class="sep">|</span>Our Founder<span class="sep">|</span>Insights<span class="sep">|</span>Contact</nav>
  <div class="rule"></div>
  <div class="copyright">Copyrights © 2018, Bluefinch Advisory Partners. All rights reserved.</div>
  <div class="social"><span></span><span></span><span></span><span></span></div>
</footer>

</body>
</html>
```